Wed site for biomedical device startup

We need a generic website for a medical device startup. I will provide examples below of websites from other companies that can serve as models for what we are looking for. The startup is for a device that can non invasively measure blood flow in the brain using light. The application is to detect the type of stroke someone is having before they get to the hospital so treatment can be started right away. This saves patients upto hours of delayed treatment. Patients will be able to recover from stroke much better and faster as a result. I have attached an AI generated illustration of what the device will ultimately look like for reference.

https://www.372clinicaltech.com
https://vextalune.com

Target Market(s)

Biomedical, medical device, investors of biomedical device startups

Industry/Entity Type

Biomedical

Coding

Coded - Design and coding required

Number of Pages Required

4 page

Requirements
Must have
• same section and section headings as example websites listed above
Nice to have
• similar to example websites listed above. Prefer a darker website over a lighter one. Perhaps dark blues to go with logo colors. A moving background image element at top of landing page could be cool. Something indicative of heartbeat, or neurons, or blood flow.

```html
<!DOCTYPE html>
<html lang="en">
<head>
<meta charset="utf-8">
<title>NOVRA — Improving the Future for the Smallest Patients</title>
<link href="https://fonts.googleapis.com/css2?family=Syncopate:wght@400;700&family=Montserrat:wght@400;500;600;700&display=swap" rel="stylesheet">
<style>
:root{
  --navy:#110f45;
  --navy-deep:#0b0a33;
  --navy-panel:#16145a;
  --cyan:#12d6e6;
  --cyan-soft:#3ec8f0;
  --purple:#8b3fe0;
  --violet:#6a4cf0;
  --white:#ffffff;
  --muted:#c9c8ee;
}
*{margin:0;padding:0;box-sizing:border-box}
html,body{width:1200px;height:5111px;overflow:hidden}
body{background:var(--navy);color:var(--white);font-family:"Montserrat",sans-serif;position:relative}
.abs{position:absolute}
.display{font-family:"Syncopate",sans-serif;font-weight:400;letter-spacing:2px;text-transform:uppercase;line-height:1.3}
.display b{font-weight:700}
.pill{position:absolute;display:flex;align-items:center;justify-content:center;border-radius:30px;font-size:12px;font-weight:700;letter-spacing:.5px;color:var(--white)}
.pill.outline{border:2px solid var(--white)}
.pill.grad{background:linear-gradient(90deg,var(--cyan),var(--purple))}
.pill.cyan{background:linear-gradient(90deg,var(--cyan),#3aa8f2)}
.rule{position:absolute;height:1px;background:var(--violet)}
.dot{position:absolute;width:8px;height:8px;border-radius:50%;background:var(--violet)}
p{line-height:1.75}

/* hero */
.hero{left:0;top:0;width:1200px;height:715px;background:radial-gradient(ellipse at 70% 30%,#2b6fd6 0%,#15308f 35%,#0d1560 70%,#0a0d45 100%)}
.nav{left:100px;top:0;width:990px;height:105px;background:rgba(12,14,60,.85)}
.brand{position:absolute;display:flex;align-items:center;gap:10px;font-weight:600;letter-spacing:2px;color:var(--white)}
.brand i{display:block;border-radius:50%;background:linear-gradient(135deg,var(--cyan),var(--purple))}
.nav-links{position:absolute;left:300px;top:52px;display:flex;gap:28px;font-size:12px;font-weight:700}
.nav-links span.sep{color:#6a6aa8;font-weight:400}
.hero-kicker{left:110px;top:272px;font-size:16px;letter-spacing:2.5px;display:flex;align-items:center;gap:10px}
.hero-kicker:after{content:"";width:38px;height:1px;background:var(--cyan)}
.hero-title{left:108px;top:308px;font-size:36px;line-height:1.32}

/* help */
.help-shape{left:0;top:715px;width:460px;height:627px}
.help-title{left:610px;top:830px;font-size:31px;background:linear-gradient(90deg,var(--cyan),var(--purple));-webkit-background-clip:text;background-clip:text;-webkit-text-fill-color:transparent}
.help-copy{left:610px;top:892px;width:540px;font-size:15px}
.help-copy p+p{margin-top:26px}

/* life */
.life-title{left:108px;top:1468px;font-size:30px}
.life-sub{left:110px;top:1585px;font-size:21px;font-weight:500}
.bullets{list-style:none;font-size:15px;font-weight:500}
.bullets li{position:relative;padding-left:18px;margin-bottom:14px}
.bullets li:before{content:"";position:absolute;left:2px;top:7px;width:6px;height:6px;background:var(--violet)}

/* explained */
.explain-panel{left:602px;top:1950px;width:598px;height:596px;background:linear-gradient(135deg,#3c63db 0%,#6b55e6 45%,#9a3ee0 100%)}
.explain-title{left:678px;top:2078px;font-size:28px}
.explain-lead{left:678px;top:2135px;width:470px;font-size:17px;line-height:1.55}
.explain-copy{left:678px;top:2215px;width:470px;font-size:15px;line-height:1.75}

/* innovative */
.kicker{font-size:14px;font-weight:700;letter-spacing:.5px;color:var(--violet)}
.feature{position:absolute;width:300px;text-align:center}
.feature h3{font-size:18px;font-weight:700;margin-top:14px}
.feature p{font-size:11px;line-height:1.55;color:var(--muted);margin:10px auto 0;width:230px}
.feature .icon{width:76px;height:76px;border-radius:50%;margin:0 auto;display:flex;align-items:center;justify-content:center}

/* standards */
.std-bg{position:absolute;top:3248px;height:482px}
.std-text{position:absolute;top:3328px;width:440px}
.std-text h2{font-size:24px}
.std-text h4{font-size:13px;font-weight:700;margin-top:30px;letter-spacing:.3px}
.std-text ul{list-style:none;margin-top:20px;font-size:16px;font-weight:500}
.std-text li{margin-bottom:11px;position:relative;padding-left:16px}
.std-text li:before{content:"";position:absolute;left:0;top:9px;width:4px;height:4px;border-radius:50%;background:var(--white)}

/* publications */
.pub{position:absolute;top:3910px;width:300px;height:245px;border:1px solid #3e3b8c;background:var(--navy-deep);padding:36px 40px 0 42px}
.pub .date{display:inline-block;background:var(--violet);font-size:10px;font-weight:700;padding:4px 10px}
.pub h3{font-size:14px;font-weight:600;line-height:1.3;margin-top:12px;letter-spacing:-.1px}
.pub p{font-size:10px;line-height:1.55;color:var(--muted);margin-top:10px}
.pub a{display:block;margin-top:12px;font-size:11px;font-weight:700;color:var(--cyan-soft);text-decoration:underline}

/* contact */
.contact-info{font-size:18px}
.form{left:602px;top:4375px;width:526px;height:457px;background:linear-gradient(160deg,#18c8ea 0%,#4a78e6 50%,#8a45df 100%)}
.field{position:absolute;background:var(--white);color:#4b4b7a;font-size:12px;display:flex;align-items:flex-start;gap:8px;padding:14px 14px}
.send{position:absolute;left:53px;top:380px;width:188px;height:42px;background:var(--navy);font-size:12px;font-weight:700;display:flex;align-items:center;justify-content:center;gap:6px}

/* footer */
.footer{left:0;top:4902px;width:1200px;height:209px;background:var(--navy-deep)}
.footer-links{position:absolute;left:475px;top:66px;display:flex;gap:46px;font-size:13px;font-weight:700}
.legal{position:absolute;font-size:11px;color:#9c9bd0}
</style>
</head>
<body>

<!-- HERO -->
<section class="abs hero" role="img" aria-label="Glowing blue neuron network background"></section>
<header class="abs nav">
  <div class="brand" style="left:35px;top:32px;font-size:32px"><i style="width:40px;height:40px"></i>NOVRA</div>
  <nav class="nav-links">
    <span>HOME</span><span class="sep">|</span><span>ABOUT</span><span class="sep">|</span><span>TECHNOLOGY</span><span class="sep">|</span><span>PUBLICATIONS</span>
  </nav>
  <a class="pill grad" style="left:845px;top:42px;width:145px;height:38px">CONTACT US ›</a>
</header>
<div class="abs hero-kicker">WELCOME TO NOVRA</div>
<h1 class="abs display hero-title">Improving the<br>future for the<br><b>smallest patients</b></h1>
<a class="pill outline" style="left:110px;top:470px;width:176px;height:42px">LEARN MORE ›</a>
<div class="abs" style="left:602px;top:650px;width:1px;height:80px;background:#c9c8ee"></div>
<div class="dot" style="left:598px;top:726px;background:#fff"></div>

<!-- HOW WE HELP -->
<svg class="abs help-shape" viewBox="0 0 460 627" aria-hidden="true">
  <defs><linearGradient id="helpGrad" x1="0" y1="1" x2="1" y2="0"><stop offset="0" stop-color="#12d6e6"/><stop offset=".55" stop-color="#3f8fe8"/><stop offset="1" stop-color="#8b3fe0"/></linearGradient></defs>
  <polygon points="0,0 456,0 238,627 0,627" fill="url(#helpGrad)"/>
</svg>
<svg class="abs" style="left:80px;top:800px" width="480" height="480" viewBox="0 0 480 480" aria-hidden="true">
  <circle cx="240" cy="240" r="232" fill="none" stroke="#5a62d8" stroke-width="2"/>
  <circle cx="94" cy="44" r="4" fill="#fff"/>
</svg>
<div class="abs" role="img" aria-label="Patient seated wearing a cerebral monitoring headset" style="left:112px;top:832px;width:416px;height:416px;border-radius:50%;background:radial-gradient(circle at 45% 40%,#e6e8ee 0%,#b9bfcc 55%,#7d86a0 100%)"></div>
<div class="abs" aria-hidden="true" style="left:437px;top:1117px;width:96px;height:96px;border-radius:50%;background:linear-gradient(135deg,#1a1560,#3b2a9a);border:2px solid var(--cyan)"></div>
<h2 class="abs display help-title">How we help</h2>
<div class="rule" style="left:970px;top:854px;width:230px"></div><div class="dot" style="left:965px;top:850px"></div>
<div class="abs help-copy">
  <p>During the first days of life, a significant risk of permanent injury exists from ventricular hemorrhage (IVH), caused by rupture of immature blood vessels in the brain due to excessive flow. There is a clear link between excessive fluctuations in blood flow and subsequent development of IVH.</p>
  <p>NOVRA is a continuous intracranial blood flow sensor designed to provide real-time monitoring of blood flow, &nbsp;providing clinicians with an early warning signal to potentially mitigate permanent injury.</p>
</div>
<a class="pill cyan" style="left:610px;top:1199px;width:182px;height:40px">LEARN MORE ›</a>

<!-- LIFE-CHANGING TECHNOLOGY -->
<div class="abs" role="img" aria-label="Glowing red human heart and circulatory system" style="left:560px;top:1342px;width:640px;height:608px;background:radial-gradient(ellipse at 55% 55%,#c21e3a 0%,#6b1242 30%,#25134f 60%,var(--navy) 80%)"></div>
<div class="rule" style="left:0;top:1488px;width:85px"></div><div class="dot" style="left:82px;top:1484px"></div>
<h2 class="abs display life-title">Life-changing<br>technology</h2>
<div class="abs life-sub">What is it LUMERA</div>
<ul class="abs bullets" style="left:110px;top:1632px">
  <li>Non- invasive real- time cerebral blood flow device</li>
  <li>Technology validated in 1,000+ children</li>
  <li>Exclusive IP license from Harborview Academic Hospital</li>
  <li>Currently in clinical evaluation</li>
</ul>

<!-- LUMERA EXPLAINED -->
<div class="abs" role="img" aria-label="Illuminated human brain with glowing neural pathways" style="left:0;top:1950px;width:602px;height:596px;background:radial-gradient(ellipse at 45% 50%,#b04a7a 0%,#5a3a9a 35%,#1d3f7a 65%,#101a4a 100%)"></div>
<div class="abs explain-panel"></div>
<h2 class="abs display explain-title">LUMERA <b>explained</b></h2>
<div class="rule" style="left:1085px;top:2092px;width:115px;background:#b8c4ff"></div><div class="dot" style="left:1077px;top:2088px;background:#b8c4ff"></div>
<p class="abs explain-lead">Our probe delivers a small amount of coherent, red light through the skin.</p>
<p class="abs explain-copy">The resulting reflection pattern has a variable intensity, called speckle, that changes from the motion of red blood cells in the field of exposure. We use a computational algorithm to resolve the relative amount of motion that directly correlates to the blood flow.</p>
<a class="pill outline" style="left:678px;top:2385px;width:162px;height:38px;font-size:11px">LEARN MORE ›</a>

<!-- INNOVATIVE -->
<div class="abs" style="left:602px;top:2546px;width:1px;height:50px;background:var(--violet)"></div>
<div class="dot" style="left:598px;top:2594px"></div>
<div class="abs kicker" style="left:0;top:2638px;width:1200px;text-align:center">ADVANCED TECHNOLOGY</div>
<h2 class="abs display" style="left:0;top:2668px;width:1200px;text-align:center;font-size:30px">Innovative blood loss<br>monitoring</h2>
<svg class="abs" style="left:0;top:2770px" width="1200" height="410" viewBox="0 0 1200 410" aria-hidden="true">
  <defs><linearGradient id="diaGrad" x1="0" y1="0" x2="1" y2="1"><stop offset="0" stop-color="#12d6e6"/><stop offset=".5" stop-color="#4a82e8"/><stop offset="1" stop-color="#8b3fe0"/></linearGradient></defs>
  <path d="M255 12 L443 200 L255 388 L67 200 Z" fill="none" stroke="#fff" stroke-width="1.3" stroke-linejoin="round"/>
  <path d="M965 12 L1153 200 L965 388 L777 200 Z" fill="none" stroke="#fff" stroke-width="1.3" stroke-linejoin="round"/>
  <path d="M608 12 L796 200 L608 388 L420 200 Z" fill="url(#diaGrad)" stroke="url(#diaGrad)" stroke-width="16" stroke-linejoin="round"/>
</svg>
<div class="feature" style="left:105px;top:2862px">
  <div class="icon" style="background:var(--cyan)"><svg width="40" height="40" viewBox="0 0 40 40" fill="none" stroke="#fff" stroke-width="2"><path d="M17 6 C11 15 8 20 8 25 a9 9 0 0 0 18 0 C26 20 23 15 17 6Z"/><path d="M12 26 h4 l2-4 2 7 2-3 h3"/></svg></div>
  <h3>Portable Monitoring</h3>
  <p>Compact, wearable devices that provide continuous blood loss monitoring anywhere, anytime.</p>
</div>
<div class="feature" style="left:458px;top:2862px">
  <div class="icon" style="background:var(--navy)"><svg width="40" height="40" viewBox="0 0 40 40" fill="none" stroke="#fff" stroke-width="2"><path d="M12 27 V18 a8 8 0 0 1 16 0 V27 l3 3 H9 Z"/><path d="M17 33 a3 3 0 0 0 6 0"/><path d="M20 7 v3"/></svg></div>
  <h3>Real-time Alerts</h3>
  <p>Compact, wearable devices that provide continuous blood loss monitoring anywhere, anytime.</p>
</div>
<div class="feature" style="left:815px;top:2862px">
  <div class="icon" style="background:var(--purple)"><svg width="40" height="40" viewBox="0 0 40 40" fill="none" stroke="#fff" stroke-width="2"><circle cx="20" cy="13" r="6"/><path d="M9 33 c0-7 5-11 11-11 s11 4 11 11"/><path d="M26 6 h6 M29 3 v6"/></svg></div>
  <h3>Patient-Centered</h3>
  <p>Easy-to-use interface designed for both patients and healthcare providers.</p>
</div>

<!-- STANDARDS OF CARE -->
<div class="std-bg" role="img" aria-label="Clinician performing a transcranial ultrasound, purple tint" style="left:0;width:608px;background:linear-gradient(120deg,#9a4ae8 0%,#6f55e4 55%,#5a52d8 100%)"></div>
<div class="std-bg" role="img" aria-label="Modern hospital room, cyan tint" style="left:608px;width:592px;background:linear-gradient(120deg,#2bb7ea 0%,#49b3ee 50%,#6fc0ee 100%)"></div>
<div class="std-text" style="left:132px">
  <h2 class="display">Current standard<br>of care</h2>
  <h4>TRANSCRANIAL DOPPLER ULTRASOUND</h4>
  <ul>
    <li>Measures speed not flow</li>
    <li>Not continuous</li>
    <li>Discovers damage after it is irreversible</li>
    <li>Bulky, interferes with other monitoring</li>
    <li>Detects only larger vessels</li>
  </ul>
</div>
<div class="std-text" style="left:712px">
  <h2 class="display">Future standard<br>of care</h2>
  <h4>LUMERA</h4>
  <ul style="padding-left:16px">
    <li>Continuous measurement</li>
    <li>Detects issues early</li>
    <li>Can measure cortical blood flow</li>
    <li>For use in small vessels</li>
  </ul>
</div>
<div class="abs" aria-hidden="true" style="left:568px;top:3440px;width:80px;height:80px;border-radius:50%;background:rgba(255,255,255,.14);border:2px solid #fff"></div>

<!-- PUBLICATIONS -->
<h2 class="abs display" style="left:98px;top:3840px;font-size:30px">Publications</h2>
<article class="pub" style="left:95px"><span class="date">10 APR 2025</span><h3>Lorem ipsum dolor sit amet, consectetur adipiscing</h3><p>elit, sed do eiusmod tempor incididunt ut labore et dolore magna aliqua. Quis ipsum suspendisse ultrices gravida.vel facilisis.</p><a>LEARN MORE</a></article>
<article class="pub" style="left:425px"><span class="date">04 APR 2025</span><h3>Lorem ipsum dolor sit amet, consectetur adipiscing</h3><p>elit, sed do eiusmod tempor incididunt ut labore et dolore magna aliqua. Quis ipsum suspendisse ultrices gravida.vel facilisis.</p><a>LEARN MORE</a></article>
<article class="pub" style="left:755px"><span class="date">02 APR 2025</span><h3>Lorem ipsum dolor sit amet, consectetur adipiscing</h3><p>elit, sed do eiusmod tempor incididunt ut labore et dolore magna aliqua. Quis ipsum suspendisse ultrices gravida.vel facilisis.</p><a>LEARN MORE</a></article>
<article class="pub" style="left:1085px"><span class="date">01 APR 2025</span><h3>Lorem ipsum dolor sit amet, consectetur adipiscing</h3><p>elit, sed do eiusmod tempor incididunt ut labore et dolore magna aliqua. Quis ipsum suspendisse ultrices gravida.vel facilisis.</p><a>LEARN MORE</a></article>
<div class="abs" style="left:525px;top:4198px;width:35px;height:3px;background:var(--cyan-soft)"></div>
<div class="abs" style="left:575px;top:4198px;width:35px;height:3px;background:#2c2a75"></div>
<div class="abs" style="left:625px;top:4198px;width:35px;height:3px;background:#2c2a75"></div>

<!-- CONTACT -->
<div class="abs kicker" style="left:135px;top:4402px;color:var(--cyan-soft);letter-spacing:2px">GET IN TOUCH</div>
<div class="rule" style="left:0;top:4445px;width:115px;background:var(--cyan-soft)"></div><div class="dot" style="left:112px;top:4441px;background:var(--cyan-soft)"></div>
<h2 class="abs display" style="left:135px;top:4428px;font-size:30px">Contact <b>us</b></h2>
<p class="abs" style="left:138px;top:4500px;width:420px;font-size:15px;line-height:1.8">Fill out the contact form or call us at (555) 014-2270 to schedule your consultation.</p>
<div class="abs contact-info" style="left:140px;top:4590px;display:flex;gap:18px">
  <svg width="22" height="30" viewBox="0 0 22 30"><path d="M11 1 a10 10 0 0 1 10 10 c0 7-10 18-10 18 S1 18 1 11 A10 10 0 0 1 11 1Z" fill="var(--cyan-soft)"/><circle cx="11" cy="11" r="4" fill="var(--navy)"/></svg>
  <div style="line-height:1.35">Address<br>214 Linden Ave, Fairhaven, AL 36990</div>
</div>
<div class="abs contact-info" style="left:140px;top:4660px;display:flex;gap:18px;align-items:center">
  <svg width="24" height="24" viewBox="0 0 24 24"><path d="M5 2 h4 l2 5 -3 2 a12 12 0 0 0 7 7 l2-3 5 2 v4 a2 2 0 0 1-2 2 A19 19 0 0 1 3 4 a2 2 0 0 1 2-2Z" fill="var(--cyan-soft)"/></svg>
  <span>Phone: (555) 014-2270</span>
</div>
<div class="abs contact-info" style="left:140px;top:4708px;display:flex;gap:18px;align-items:center">
  <svg width="24" height="18" viewBox="0 0 24 18"><rect x="0" y="0" width="24" height="18" rx="2" fill="var(--cyan-soft)"/><path d="M1 2 L12 10 L23 2" fill="none" stroke="var(--navy)" stroke-width="2"/></svg>
  <span>hello@novra-med.com</span>
</div>
<form class="abs form">
  <div class="field" style="left:53px;top:70px;width:210px;height:44px">👤&#xFE0E; First Name</div>
  <div class="field" style="left:272px;top:70px;width:211px;height:44px">👤&#xFE0E; Last Name</div>
  <div class="field" style="left:53px;top:126px;width:430px;height:44px">✉&#xFE0E; Email address</div>
  <div class="field" style="left:53px;top:183px;width:430px;height:44px">✆&#xFE0E; Phone Number</div>
  <div class="field" style="left:53px;top:240px;width:430px;height:112px">✎&#xFE0E; Leave Message</div>
  <div class="send">SEND MESSAGE ›</div>
</form>

<!-- FOOTER -->
<footer class="abs footer">
  <div class="brand" style="left:145px;top:50px;font-size:34px"><i style="width:54px;height:54px"></i>NOVRA</div>
  <nav class="footer-links"><span>HOME</span><span>ABOUT</span><span>TECHNOLOGY</span><span>PUBLICATIONS</span><span>CONTACT US</span></nav>
  <div class="abs" style="left:140px;top:130px;width:930px;height:1px;background:#24226a"></div>
  <div class="legal" style="left:140px;top:148px">© 2025 NOVRA | All Rights Reserved</div>
  <div class="legal" style="left:845px;top:148px">Privacy Policy</div>
  <div class="legal" style="left:967px;top:148px">Terms of Service</div>
</footer>

</body>
</html>
```